Quote Cards With KB May 2025 for Instagram

I would like to put these quotes over one of the pictures attached; Instagram (new size: 4:5 (1080 x 1350 pixels) One Quote per picture, and I want the quote to be bold or easy to read as well. I provided a few reference graphics that I really like as examples below. In very small letters at the bottom add @KBHarlowOnline

All of the pictures are attached; you can pick any photo and add one quote to it; but no stock photography

```html
<!DOCTYPE html>
<html lang="en">
<head>
<meta charset="utf-8">
<title>Quote Card – Stubborn Weight</title>
<link rel="stylesheet" href="https://fonts.googleapis.com/css2?family=Bebas+Neue&display=swap">
<style>
  :root {
    --magenta: #e0288f;
    --magenta-deep: #c41c82;
    --pink-light: #f4b3dc;
    --pink-mid: #d968b4;
    --violet: #9a4a9c;
    --panel-top: rgba(125, 35, 75, 0.80);
    --panel-mid: rgba(45, 12, 32, 0.90);
    --panel-low: rgba(14, 5, 11, 0.94);
    --panel-bottom: rgba(22, 7, 16, 0.90);
    --text: #ffffff;
  }
  * { margin: 0; padding: 0; box-sizing: border-box; }
  html, body { width: 960px; height: 1200px; overflow: hidden; background: #1a0812; }
  .card {
    position: relative;
    width: 960px;
    height: 1200px;
    overflow: hidden;
    font-family: "Bebas Neue", "Oswald", sans-serif;
    color: var(--text);
  }
  .card__stage {
    position: absolute;
    inset: 0;
    background:
      radial-gradient(ellipse 380px 460px at 900px 380px, var(--pink-light) 0%, rgba(244,179,220,0) 100%),
      radial-gradient(ellipse 300px 260px at 60px 620px, rgba(240,70,160,0.9) 0%, rgba(240,70,160,0) 100%),
      linear-gradient(180deg, var(--pink-mid) 0%, #c058a8 45%, var(--violet) 75%, #3a1230 100%);
  }
  .card__subject {
    position: absolute;
    left: 578px;
    top: 84px;
    width: 300px;
    height: 1116px;
    border-radius: 150px 150px 40px 40px;
    background: linear-gradient(180deg, #5a1a3a 0%, #7a2250 14%, var(--magenta) 26%, #e8309c 55%, var(--magenta-deep) 100%);
  }
  .card__panel {
    position: absolute;
    left: 34px;
    top: 0;
    width: 540px;
    height: 1200px;
    background: linear-gradient(180deg, var(--panel-top) 0%, rgba(90,25,60,0.85) 22%, var(--panel-mid) 40%, var(--panel-low) 49%);
  }
  .card__panel-lower {
    position: absolute;
    left: 34px;
    top: 587px;
    width: 540px;
    height: 613px;
    background: linear-gradient(180deg, rgba(8,3,7,0.96) 0%, rgba(30,10,24,0.88) 40%, var(--panel-bottom) 100%);
  }
  .quote {
    position: absolute;
    left: 73px;
    text-transform: uppercase;
    font-weight: 400;
  }
  .quote--lead { top: 94px; font-size: 74px; line-height: 76px; }
  .quote--reason { top: 437px; font-size: 74px; line-height: 78px; }
  .quote--promise { top: 812px; font-size: 106px; line-height: 102px; }
  .handle {
    position: absolute;
    left: 73px;
    top: 1104px;
    font-size: 30px;
    line-height: 1;
    letter-spacing: -0.3px;
  }
</style>
</head>
<body>
  <main class="card">
    <div class="card__stage"></div>
    <div class="card__subject" role="img" aria-label="Photo of a smiling woman in a long pink gown standing on a pink-lit stage"></div>
    <div class="card__panel"></div>
    <div class="card__panel-lower"></div>
    <p class="quote quote--lead">That stubborn<br>weight?<br>It’s not your fault.</p>
    <p class="quote quote--reason">Your hormones<br>are to blame<br>and you’re<br>not alone</p>
    <p class="quote quote--promise">But there is<br>a fix.</p>
    <p class="handle">@KBHARLOWONLINE</p>
  </main>
</body>
</html>
```